BUSINESS CARD DESIGN

NAME- DALE VORSKIN
PHONE NUMER - 555- 714-9082
EMAIL- OFFICE@TRV-GROUNDMAKRZ.COM
BACK OF CARD- SPEACIALIZES IN LAND CLEARING, FORESTRY MUCLHING AND EXCAVATION

Contact Information for Business Card

NAME- DALE VORSKIN PHONE NUMER - 555- 714-9082 EMAIL- OFFICE@TRV-GROUNDMAKRZ.COM BACK OF CARD- SPEACIALIZES IN LAND CLEARING , MUCLHING AND EXCAVATION

```html
<!DOCTYPE html>
<html lang="en">
<head>
<meta charset="utf-8">
<title>Traverse Groundmakrz – Business Card</title>
<link href="https://fonts.googleapis.com/css2?family=Montserrat:wght@400;500;700&family=Roboto:wght@400;500&display=swap" rel="stylesheet">
<style>
  :root{
    --page:#e2e2e2;
    --card-dark:#161616;
    --card-light:#ffffff;
    --ink:#111111;
    --mark-dark:#3a3a3a;
    --tagline:#4a4a4a;
    --muted:#707070;
    --body:#3c3c3c;
    --divider:#9a9a9a;
    --palm:#a3a3a3;
  }
  *{box-sizing:border-box;margin:0;padding:0}
  html,body{width:1200px;height:1200px;overflow:hidden;background:var(--page)}
  .card{position:absolute;left:180px;width:867px;height:499px;box-shadow:0 14px 22px rgba(0,0,0,.25)}
  .card--back{top:85px;background:var(--card-dark)}
  .card--front{top:625px;background:var(--card-light);overflow:hidden}

  /* back */
  .back-mark{position:absolute;left:50%;top:40px;width:210px;height:210px;margin-left:-105px;border:3px solid var(--mark-dark);border-radius:50%}
  .back-name{position:absolute;left:0;right:0;top:265px;text-align:center;font-family:"Montserrat",sans-serif;font-weight:700;font-size:26px;letter-spacing:3px;color:var(--mark-dark)}
  .back-phone{position:absolute;left:0;right:0;top:340px;text-align:center;font-family:"Montserrat",sans-serif;font-weight:700;font-size:14px;letter-spacing:12px;color:var(--mark-dark)}
  .tagline{position:absolute;left:0;right:0;top:380px;text-align:center;font-family:"Montserrat",sans-serif;font-weight:500;font-size:21px;line-height:28px;letter-spacing:1.5px;color:var(--tagline)}

  /* front */
  .palms{position:absolute;left:464px;top:253px;width:337px;height:246px;background:linear-gradient(180deg,rgba(163,163,163,.85),var(--palm));border-radius:50% 50% 0 0/40% 40% 0 0}
  .front-mark{position:absolute;left:168px;top:160px;width:100px;height:100px;border:3px solid var(--ink);border-radius:50%}
  .front-name{position:absolute;left:88px;width:262px;top:275px;text-align:center;font-family:"Montserrat",sans-serif;font-weight:700;font-size:17px;line-height:22px;letter-spacing:1px;color:var(--ink)}
  .divider{position:absolute;left:361px;top:153px;width:1px;height:188px;background:var(--divider)}
  .contact{position:absolute;left:384px;top:150px;font-family:"Roboto",sans-serif;color:var(--body)}
  .contact__name{font-family:"Montserrat",sans-serif;font-weight:700;font-size:30px;letter-spacing:.5px;color:var(--ink);line-height:36px}
  .contact__role{font-family:"Montserrat",sans-serif;font-size:21px;letter-spacing:1px;color:var(--muted);line-height:26px;margin-bottom:16px}
  .contact__line{font-size:19px;letter-spacing:1.2px;line-height:29px;margin-left:2px}
  .contact__row{display:flex;align-items:center;font-size:19px;letter-spacing:1.2px;line-height:29px;margin-top:0}
  .contact__row:first-of-type{margin-top:10px}
  .contact__row svg{width:20px;height:20px;margin-right:18px;flex:none}
</style>
</head>
<body>
  <section class="card card--back">
    <div class="back-mark"></div>
    <div class="back-name">TRAVERSE GROUNDMAKRZ LLC</div>
    <div class="back-phone">555-714-9082</div>
    <p class="tagline">SPEACIALIZES IN LAND CLEARING , MUCLHING<br>AND EXCAVATION</p>
  </section>

  <section class="card card--front">
    <div class="palms" role="img" aria-label="Grey silhouette of palm trees"></div>
    <div class="front-mark"></div>
    <div class="front-name">TRAVERSE<br>GROUNDMAKRZ LLC</div>
    <div class="divider"></div>
    <div class="contact">
      <h1 class="contact__name">DALE VORSKIN</h1>
      <p class="contact__role">DIRECTOR</p>
      <p class="contact__line">123 Anywhere St.</p>
      <p class="contact__line">Any City, ST 12345</p>
      <p class="contact__row">
        <svg viewBox="0 0 24 24" aria-hidden="true"><path d="M6.6 10.8a15 15 0 0 0 6.6 6.6l2.2-2.2c.3-.3.7-.4 1-.2 1.1.4 2.3.6 3.6.6.6 0 1 .4 1 1V20c0 .6-.4 1-1 1A17 17 0 0 1 3 4c0-.6.4-1 1-1h3.5c.6 0 1 .4 1 1 0 1.3.2 2.5.6 3.6.1.3 0 .7-.2 1z" fill="none" stroke="#111" stroke-width="1.8"/></svg>
        555- 714-9082
      </p>
      <p class="contact__row">
        <svg viewBox="0 0 24 24" aria-hidden="true"><rect x="2" y="5" width="20" height="14" fill="#111"/><path d="M2 5l10 8 10-8" fill="none" stroke="#fff" stroke-width="1.5"/></svg>
        OFFICE@TRV-GROUNDMAKRZ.COM
      </p>
    </div>
  </section>
</body>
</html>
```